Lone Star Wetland Flora Stewardship Guild

We need to design the home page of this new website. We would like a fun website design for provides as a resource for members and information for potential members.
Please design so that we can see a portion of background on each side on the website.
I just need the final design files psd no coding needed.
Attached is their logo (colors are not 100% set in stone either so can mess with those as I did in the quick mockup attached)
Attached is a pdf newsletter they send out, you can get a feel for them and what they are about. The design is crappy and we are here to fix that going forward and we are starting with the website.
Here are some quick example websites (design style is open)
- I attached a quick mockup i did just for a content visual but by all means do what you want.
- http://www.brightpathleaders.example/
- http://www.civicunityhub.example/
- http://preview.webskinvault.example/show.php?cat=layouts&host=skinbazaar&temp=novaline
- http://www.meadowkeep.example/
- http://www.urbangleaners.example/
- http://www.projectcozyknit.example/
here are some of the other chapters website (pretty bad!)
and here are some of the others:
- http://www.dwrvcs.example/
- http://kwfg.example/
- http://www.blvcg.example/
Content Items that need to be included:
1. Logo
2. Menu - home, about, members, resources, events, membership, contact
3. Become a member - button or action
4. social links - chatterloop, workweave, clipstream
5. banner - that needs to explain their purpose "Promoting environmental stewardship through operations, research, education and outreach" (or this can be worked into the design)
6. Upcoming event (s)
7. Advertisement - members can place an ad on the website, this can be a placeholder for now
8. newsletter signup
9. advertise with us - this link can be in the footer
30-60 years of age, succesfull (household budgets of 120K+ men and women that live in texas.
Education

```html
<!DOCTYPE html>
<html lang="en">
<head>
<meta charset="utf-8">
<title>Lone Star Wetland Flora Stewardship Guild</title>
<link rel="stylesheet" href="https://fonts.googleapis.com/css2?family=Raleway:wght@400;500;600;800&family=Source+Sans+3:ital,wght@0,400;0,600;1,400&family=Arimo:wght@400;700&display=swap">
<style>
:root{
  --navy:#0b2a6e;
  --navy-deep:#031a4a;
  --crimson:#b02a4e;
  --crimson-deep:#8f1d3c;
  --ink:#2b2b2b;
  --muted:#c9cdd6;
}
*{box-sizing:border-box;margin:0;padding:0}
html,body{width:1200px;height:1094px;overflow:hidden}
body{position:relative;background:linear-gradient(#dedede 0,#f3f3f3 420px,#fff 600px);font-family:"Source Sans 3",sans-serif;color:var(--ink)}
.abs{position:absolute}
.site-title{left:265px;top:29px;width:475px;text-align:right;font:500 23px "Raleway",sans-serif;color:#1a1a1a;white-space:nowrap}
.social{left:754px;top:38px;display:flex;gap:9px;font:600 11px "Source Sans 3",sans-serif;color:#1a1a1a;white-space:nowrap}
.social span{display:flex;align-items:center;gap:4px}
.social i{width:9px;height:9px;border-radius:50%;background:#111;display:block}
.divider{left:989px;top:22px;width:1px;height:48px;background:#c4c4c4}
.login{left:1005px;top:38px;display:flex;align-items:center;gap:9px;font:15px "Arimo",sans-serif;color:#222}
.logo{left:104px;top:80px;display:flex;align-items:center;gap:10px;font:800 44px "Raleway",sans-serif;color:var(--crimson);letter-spacing:-0.5px;line-height:50px}
.logo i{width:22px;height:22px;background:var(--navy);border-radius:50%;display:block}
.main-nav{left:348px;top:78px;width:752px;height:55px;border-radius:22px;background:linear-gradient(#0d2f7a,#021645);display:flex;align-items:center;justify-content:space-between;padding:0 32px 0 30px}
.main-nav a{color:#fff;text-decoration:none;font:14.5px "Arimo",sans-serif}
.newsletter-label{left:693px;top:146px;font:500 21px "Raleway",sans-serif;color:var(--navy-deep)}
.newsletter-input{left:824px;top:146px;width:165px;height:31px;border:1px solid #cfcfcf;background:#fff;font:13px "Arimo",sans-serif;color:#777;padding:7px 6px}
.signup{left:1001px;top:146px;width:98px;height:31px;border-radius:4px;background:linear-gradient(#c0375b,var(--crimson-deep));color:#fff;font:600 15px "Raleway",sans-serif;letter-spacing:.5px;text-align:center;line-height:31px}
.hero{left:100px;top:190px;width:1000px;height:421px;background:
  radial-gradient(ellipse at 70% 70%,#5fa04a 0,transparent 45%),
  radial-gradient(ellipse at 20% 85%,#6db552 0,transparent 40%),
  linear-gradient(#9cc7c0 0,#6c9d97 35%,#3f5a4d 60%,#4d7a3a 100%)}
.hero-band{left:100px;top:290px;width:1000px;height:91px;background:rgba(20,25,25,.55)}
.hero-text{left:300px;top:300px;width:781px;text-align:right;font:500 25px/34px "Raleway",sans-serif;color:#fff;letter-spacing:.3px}
.col-head{height:52px;color:#fff;font:500 28px "Raleway",sans-serif;padding-left:16px;line-height:52px;white-space:nowrap}
.col-head.navy{background:linear-gradient(#0e3a8c,#021645)}
.col-head.crimson{background:linear-gradient(#c6456a,#a51f45);padding-left:21px;font-size:26px}
.about-text{left:105px;top:706px;width:290px;font:15px/22px "Source Sans 3",sans-serif}
.btn-dark{left:291px;top:954px;width:107px;height:28px;border-radius:4px;background:#2e2e2e;color:#fff;font:700 14px "Arimo",sans-serif;text-align:center;line-height:28px}
.event{left:443px;width:345px;display:flex;gap:14px}
.event .thumb{width:96px;height:64px;flex:none;background:linear-gradient(#8fb8df 0,#cfe0ea 35%,#6f8f4a 55%,#3e5f48 100%)}
.event h3{font:600 15px "Source Sans 3",sans-serif;color:var(--navy);margin-top:-3px}
.event .date{font:italic 15px "Source Sans 3",sans-serif;color:var(--crimson);line-height:19px}
.event p{font:14px/18px "Source Sans 3",sans-serif;margin-top:-1px;max-width:222px}
.view-all{left:719px;top:982px;font:700 14px "Arimo",sans-serif;color:#111}
.ad-photo{left:825px;top:710px;width:274px;height:231px;background:radial-gradient(ellipse at 60% 20%,#2f7fb8 0,#0c3b66 50%,#12161c 100%)}
.ad-brand{left:825px;top:941px;width:274px;height:62px;background:#d6d6d6;font:700 22px "Source Sans 3",sans-serif;color:#1a1a1a;text-align:center;line-height:62px}
.footer{left:0;top:1042px;width:1200px;height:52px;background:var(--navy-deep)}
.copyright{left:107px;top:1055px;font:14px "Arimo",sans-serif;color:var(--muted)}
.advertise{left:968px;top:1055px;font:16px "Arimo",sans-serif;color:var(--muted);text-decoration:underline}
</style>
</head>
<body>
<header>
  <div class="abs site-title">Lone Star Wetland Flora Stewardship Guild</div>
  <nav class="abs social" aria-label="Social links">
    <span><i></i>chatterloop</span><span><i></i>workweave</span><span><i></i>clipstream</span>
  </nav>
  <div class="abs divider"></div>
  <div class="abs login">
    <svg width="17" height="17" viewBox="0 0 17 17" aria-hidden="true"><path d="M6 2h9v13H6" fill="none" stroke="#b02a4e" stroke-width="1.6"/><path d="M1 8.5h9M7 5.5l3 3-3 3" fill="none" stroke="#b02a4e" stroke-width="1.6"/></svg>
    Login
  </div>
  <div class="abs logo"><i></i>LSWFSG</div>
  <nav class="abs main-nav" aria-label="Main">
    <a href="#">HOME</a><a href="#">ABOUT</a><a href="#">MEMBERS</a><a href="#">RESOURCES</a><a href="#">EVENTS</a><a href="#">MEMBERSHIP</a><a href="#">CONTACT</a>
  </nav>
  <div class="abs newsletter-label">Newsletter:</div>
  <div class="abs newsletter-input">Email Address</div>
  <div class="abs signup">SIGN UP</div>
</header>

<section>
  <div class="abs hero" role="img" aria-label="Pond with floating lily pads and tall reeds reflected in still water"></div>
  <div class="abs hero-band"></div>
  <p class="abs hero-text">Promoting environmental stewardship through operations,<br>research, education and outreach</p>
</section>

<main>
  <h2 class="abs col-head navy" style="left:100px;top:640px;width:298px">About LSWFSG</h2>
  <p class="abs about-text">The Lone Star Wetland Flora Stewardship Guild is an organization of scientists, educators, students, commercial pesticide applicators, administrators, and concerned individuals interested in the management and study of aquatic plants. The membership reflects a diversity of federal, state, and local agencies; universities and colleges around the world; corporations; and small businesses.</p>
  <div class="abs btn-dark">Read More</div>

  <h2 class="abs col-head navy" style="left:443px;top:640px;width:334px;line-height:50px">Upcoming Events</h2>
  <article class="abs event" style="top:710px">
    <div class="thumb" role="img" aria-label="Lake with lily pads under a blue sky"></div>
    <div><h3>2014 Northeast Aquatic Plant</h3><div class="date">January 21, 2014</div><p>Lorem Ipsum is simply dummy text of the printing .</p></div>
  </article>
  <article class="abs event" style="top:802px">
    <div class="thumb" role="img" aria-label="Reeds along a calm lake shore"></div>
    <div><h3>2014 Northeast Aquatic Plant</h3><div class="date">January 21, 2014</div><p>Lorem Ipsum is simply dummy text of the printing .</p></div>
  </article>
  <article class="abs event" style="top:897px">
    <div class="thumb" role="img" aria-label="Lake with lily pads under a blue sky"></div>
    <div><h3>2014 Northeast Aquatic Plant</h3><div class="date">January 21, 2014</div><p>Lorem Ipsum is simply dummy text of the printing .</p></div>
  </article>
  <a class="abs view-all">View All..</a>

  <h2 class="abs col-head crimson" style="left:825px;top:641px;width:274px">Become a Member</h2>
  <div class="abs ad-photo" role="img" aria-label="Member advertisement: ClearPond Max algaecide jug and bag on a blue water background"></div>
  <div class="abs ad-brand">AquaGuard Labs</div>
</main>

<footer>
  <div class="abs footer"></div>
  <div class="abs copyright">Copyright © 2014 LSWFSG. All rights reserved.</div>
  <a class="abs advertise">advertise with us</a>
</footer>
</body>
</html>
```